Modern & Fresh Vantacor Book Cover

Need a creative e-book cover for my book.

Title: Master Vantacor Fast
Subtitle: Learn How To Easily Choose & Enroll in the Perfect Coverage at the Perfect Time.

Target Market(s)

60-70 year olds in the United States

Font styles to use
Sans Serif

Colors
9bcb3c
33a6d7

Requirements
Must have
• Must look modern and fresh.
• Use our company colors www.Movaquill.com

```html
<!DOCTYPE html>
<html lang="en">
<head>
<meta charset="UTF-8">
<title>Master Vantacor Fast – Book Cover</title>
<link rel="stylesheet" href="https://fonts.googleapis.com/css2?family=Montserrat:wght@400;700;900&family=Allura&display=swap">
<style>
  :root {
    --stage-teal: #14abbb;
    --brand-green: #9bcb3c;
    --brand-blue: #33a6d7;
    --ink: #1c1f24;
    --cover-light: #eef3f3;
    --cover-mist: #cfe2e8;
    --cover-shadow: #8fb3c4;
    --instrument-navy: #1f3550;
  }
  * { margin: 0; padding: 0; box-sizing: border-box; }
  html, body {
    width: 1200px;
    height: 1200px;
    overflow: hidden;
    background: var(--stage-teal);
  }
  .stage {
    position: relative;
    width: 1200px;
    height: 1200px;
  }
  .book-cover {
    position: absolute;
    left: 360px;
    top: 240px;
    width: 480px;
    height: 719px;
    overflow: hidden;
    background: var(--cover-light);
  }
  .cover-photo {
    position: absolute;
    inset: 0;
    background:
      radial-gradient(ellipse 62% 40% at 80% 78%, var(--instrument-navy) 0%, rgba(31,53,80,0.55) 35%, rgba(143,179,196,0.25) 70%, rgba(0,0,0,0) 100%),
      linear-gradient(160deg, var(--cover-light) 0%, var(--cover-light) 45%, var(--cover-mist) 80%, var(--cover-shadow) 100%);
  }
  .title-main {
    position: absolute;
    top: 40px;
    left: 0;
    width: 100%;
    text-align: center;
    font-family: "Montserrat", sans-serif;
    font-weight: 900;
    font-size: 46px;
    letter-spacing: -1.5px;
    color: var(--brand-green);
    text-transform: uppercase;
    line-height: 1;
  }
  .title-script {
    position: absolute;
    top: 92px;
    left: 0;
    width: 100%;
    text-align: center;
    font-family: "Allura", cursive;
    font-size: 190px;
    color: var(--brand-blue);
    line-height: 1;
  }
  .subtitle {
    position: absolute;
    left: 44px;
    top: 330px;
    font-family: "Montserrat", sans-serif;
    font-weight: 400;
    font-size: 19px;
    line-height: 1.12;
    color: var(--ink);
  }
  .subtitle .accent-green { color: var(--brand-green); font-weight: 700; }
  .subtitle .accent-blue { color: var(--brand-blue); font-weight: 700; }
  .publisher {
    position: absolute;
    left: 22px;
    bottom: 28px;
    display: flex;
    align-items: center;
    gap: 6px;
    font-family: "Montserrat", sans-serif;
    font-weight: 700;
    font-size: 22px;
    color: var(--brand-green);
  }
  .publisher-dot {
    width: 10px;
    height: 10px;
    border-radius: 50%;
    background: var(--brand-green);
  }
</style>
</head>
<body>
  <main class="stage">
    <section class="book-cover">
      <div class="cover-photo" role="img" aria-label="Photograph of a stethoscope and blood pressure gauge on a pale blue surface"></div>
      <h1 class="title-main">Master Vantacor</h1>
      <div class="title-script">Fast</div>
      <p class="subtitle">
        Learn How To<br>
        <span class="accent-green">Easily Choose &amp; Enroll</span><br>
        <span class="accent-blue">in the Perfect Coverage</span><br>
        at the Perfect Time
      </p>
      <div class="publisher">
        <span class="publisher-dot"></span>
        <span class="publisher-name">Movaquill</span>
      </div>
    </section>
  </main>
</body>
</html>
```